Re-style home page - eye-catching and unique design for social commerce website

We need a new concept design for BrinoKet's home page.
We don't want to make huge changes but creating a more professional and eye-catching style.

We need to look very serious like a professional services company and in the same time to look like a social network for e-commerce.

Our logo is very captive and you can use to creating something of harmonious.

This is a re-style and I'm excepted to see unique and fresh design like Glimmora.

Target Market(s)

e-commerce and social

Industry/Entity Type

Social

Number of Pages Required

1 page

Font styles to use
Serif
Sans Serif

Requirements
Must have
• An eye-catching result.
• Search bar with logo and Login How it works and business
• The slogan with login and signup.
• Footer links.
Nice to have
• I would like to open the home page and see only two clear ways:
• -Consumer
• --Search
• --The slogan
• --Login and Signup
• --How it works
• -Business
• --Go to Business area
• Background: City, Shopping.
Should not have
• Scrollbar style!

```html
<!DOCTYPE html>
<html lang="en">
<head>
<meta charset="utf-8">
<title>BrinoKet – Shop directly from your profile</title>
<link href="https://fonts.googleapis.com/css2?family=Montserrat:wght@400;600;700&family=Open+Sans:wght@300;400;600&display=swap" rel="stylesheet">
<style>
  :root {
    --night: #1c1d48;
    --night-deep: #15163a;
    --dusk: #4a4276;
    --haze: #7b6f9a;
    --header-bg: rgba(28, 30, 72, 0.72);
    --field-bg: rgba(255, 255, 255, 0.16);
    --white: #ffffff;
    --ink: #3a3a3a;
    --muted: #9a9a9a;
    --signup: #d42a2a;
    --business: #7cb82f;
    --denim-dark: #2c3f63;
    --denim: #4b6288;
    --denim-light: #8ea0bd;
    --avatar: #c9b7a6;
  }
  * { box-sizing: border-box; margin: 0; padding: 0; }
  html, body { width: 1200px; height: 675px; overflow: hidden; }
  body {
    position: relative;
    font-family: "Montserrat", Arial, sans-serif;
    color: var(--white);
    background: var(--night);
  }
  .city-backdrop {
    position: absolute; inset: 0;
    background:
      radial-gradient(ellipse at 50% 20%, rgba(190,170,200,0.35), transparent 60%),
      radial-gradient(ellipse at 15% 45%, rgba(160,110,120,0.35), transparent 45%),
      linear-gradient(180deg, var(--haze) 0%, var(--dusk) 40%, var(--night) 80%, var(--night-deep) 100%);
  }
  .site-header {
    position: absolute; left: 0; top: 0; width: 1200px; height: 59px;
    background: var(--header-bg);
  }
  .brand {
    position: absolute; left: 26px; top: 14px;
    display: flex; align-items: center; gap: 8px;
    font-weight: 700; font-size: 27px; letter-spacing: -0.5px; line-height: 30px;
  }
  .brand-dot { width: 14px; height: 14px; border-radius: 50%; background: var(--white); }
  .search-field {
    position: absolute; left: 350px; top: 11px; width: 454px; height: 36px;
    background: var(--field-bg); border-radius: 3px;
    padding-left: 16px; display: flex; align-items: center;
    font-family: "Open Sans", Arial, sans-serif; font-size: 13px; color: rgba(255,255,255,0.55);
  }
  .search-icon { position: absolute; left: 816px; top: 19px; }
  .login-link {
    position: absolute; left: 871px; top: 20px;
    font-size: 13px; font-weight: 600;
  }
  .member-links { position: absolute; inset: 0; pointer-events: none; }
  .member {
    position: absolute; width: 32px; height: 32px; border-radius: 50%;
    border: 2px solid var(--white); background: var(--avatar);
    transform: translate(-50%, -50%);
  }
  .feed-card {
    position: absolute; left: 350px; top: 194px; width: 500px; height: 269px;
    border-radius: 3px; overflow: hidden;
  }
  .card-photo {
    position: absolute; inset: 0;
    background:
      radial-gradient(ellipse at 30% 60%, var(--denim-light) 0%, transparent 45%),
      linear-gradient(160deg, var(--denim) 0%, var(--denim-dark) 55%, #5b6a80 100%);
  }
  .card-shade { position: absolute; inset: 0; background: rgba(40, 50, 80, 0.25); }
  .slogan {
    position: relative; margin-top: 31px; text-align: center;
    font-family: "Open Sans", Arial, sans-serif; font-weight: 300; font-size: 28px;
  }
  .feed-label {
    position: absolute; left: 40px; top: 91px;
    font-size: 10.5px; font-weight: 600;
  }
  .select-box {
    position: absolute; top: 112px; height: 33px; width: 163px;
    background: var(--white); border-radius: 2px; color: var(--ink);
    font-family: "Open Sans", Arial, sans-serif; font-size: 12px;
    display: flex; align-items: center; padding-left: 12px; gap: 7px;
  }
  .select-box .chevron { position: absolute; right: 10px; top: 12px; }
  .select-interest { left: 36px; }
  .select-city { left: 208px; }
  .btn-signup {
    position: absolute; left: 379px; top: 112px; width: 83px; height: 33px;
    background: var(--signup); border-radius: 2px;
    display: flex; align-items: center; justify-content: center;
    font-size: 12.5px; font-weight: 600;
  }
  .btn-business {
    position: absolute; left: 161px; top: 185px; width: 179px; height: 34px;
    background: var(--business); border-radius: 2px;
    display: flex; align-items: center; justify-content: center; gap: 6px;
    font-size: 12.5px; font-weight: 600;
  }
  .how-link {
    position: absolute; left: 0; width: 100%; top: 231px; text-align: center;
    font-size: 11px; font-weight: 600;
  }
  .site-footer { position: absolute; left: 0; top: 574px; width: 1200px; text-align: center; }
  .footer-links { display: flex; justify-content: center; gap: 28px; font-size: 10.5px; font-weight: 600; }
  .footer-links a { color: var(--white); text-decoration: none; }
  .copyright { margin-top: 14px; font-size: 9.5px; font-weight: 600; }
</style>
</head>
<body>
  <div class="city-backdrop" role="img" aria-label="Blurred evening shopping street with walking crowds"></div>

  <header class="site-header">
    <div class="brand"><span>BrinoKet</span><span class="brand-dot"></span></div>
    <div class="search-field">Search keyword</div>
    <svg class="search-icon" width="20" height="20" viewBox="0 0 20 20" aria-hidden="true">
      <circle cx="8" cy="8" r="6" fill="none" stroke="#fff" stroke-width="2.6"/>
      <line x1="12.5" y1="12.5" x2="18" y2="18" stroke="#fff" stroke-width="2.8" stroke-linecap="round"/>
    </svg>
    <span class="login-link">Login</span>
  </header>

  <svg class="member-links" width="1200" height="675" aria-hidden="true">
    <g fill="none" stroke="rgba(255,255,255,0.55)" stroke-width="1.4" stroke-dasharray="2 3">
      <path d="M362 154 Q372 180 382 194"/>
      <path d="M415 176 Q410 186 405 194"/>
      <path d="M475 172 Q468 186 458 194"/>
      <path d="M310 208 Q320 228 350 236"/>
      <path d="M694 173 Q702 188 716 194"/>
      <path d="M756 156 Q766 178 772 194"/>
      <path d="M809 178 Q800 188 792 194"/>
      <path d="M870 201 Q860 218 850 228"/>
      <path d="M303 370 Q318 380 350 386"/>
      <path d="M299 441 Q310 422 350 418"/>
      <path d="M366 475 Q378 470 386 463"/>
      <path d="M896 393 Q888 410 850 418"/>
      <path d="M915 438 Q892 452 850 446"/>
      <path d="M778 486 Q772 472 752 463"/>
      <path d="M852 471 Q842 470 826 463"/>
    </g>
  </svg>

  <div class="member" style="left:362px;top:138px" role="img" aria-label="Member portrait"></div>
  <div class="member" style="left:415px;top:160px" role="img" aria-label="Member portrait"></div>
  <div class="member" style="left:475px;top:156px" role="img" aria-label="Member portrait"></div>
  <div class="member" style="left:310px;top:192px" role="img" aria-label="Member portrait"></div>
  <div class="member" style="left:694px;top:157px" role="img" aria-label="Member portrait"></div>
  <div class="member" style="left:756px;top:140px" role="img" aria-label="Member portrait"></div>
  <div class="member" style="left:809px;top:162px" role="img" aria-label="Member portrait"></div>
  <div class="member" style="left:870px;top:185px" role="img" aria-label="Member portrait"></div>
  <div class="member" style="left:303px;top:354px" role="img" aria-label="Member portrait"></div>
  <div class="member" style="left:299px;top:457px" role="img" aria-label="Member portrait"></div>
  <div class="member" style="left:366px;top:491px" role="img" aria-label="Member portrait"></div>
  <div class="member" style="left:896px;top:377px" role="img" aria-label="Member portrait"></div>
  <div class="member" style="left:915px;top:438px" role="img" aria-label="Member portrait"></div>
  <div class="member" style="left:778px;top:502px" role="img" aria-label="Member portrait"></div>
  <div class="member" style="left:852px;top:487px" role="img" aria-label="Member portrait"></div>

  <main class="feed-card">
    <div class="card-photo" role="img" aria-label="Close-up of folded denim jeans with stitching"></div>
    <div class="card-shade"></div>
    <h1 class="slogan">Shop directly from your profile</h1>
    <div class="feed-label">Setup your feed</div>
    <div class="select-box select-interest">Active life
      <svg class="chevron" width="13" height="8" viewBox="0 0 13 8" aria-hidden="true"><path d="M1 1l5.5 5.5L12 1" fill="none" stroke="#999" stroke-width="1.3"/></svg>
    </div>
    <div class="select-box select-city">
      <svg width="10" height="14" viewBox="0 0 10 14" aria-hidden="true"><path d="M5 0a5 5 0 0 0-5 5c0 3.5 5 9 5 9s5-5.5 5-9a5 5 0 0 0-5-5z" fill="#aaa"/><circle cx="5" cy="5" r="1.8" fill="#fff"/></svg>
      London
      <svg class="chevron" width="13" height="8" viewBox="0 0 13 8" aria-hidden="true"><path d="M1 1l5.5 5.5L12 1" fill="none" stroke="#999" stroke-width="1.3"/></svg>
    </div>
    <div class="btn-signup">Sign Up</div>
    <div class="btn-business">Go to Business Area
      <svg width="18" height="8" viewBox="0 0 18 8" aria-hidden="true"><path d="M0 4h16M13 1l3 3-3 3" fill="none" stroke="#fff" stroke-width="1.1"/></svg>
    </div>
    <div class="how-link">How it works</div>
  </main>

  <footer class="site-footer">
    <nav class="footer-links">
      <a href="#">About Us</a><a href="#">Blog</a><a href="#">Business</a><a href="#">Jobs</a><a href="#">Privacy</a><a href="#">FAQ</a><a href="#">Contacts</a>
    </nav>
    <p class="copyright">© 2015 BrinoKet. All right reserved.</p>
  </footer>
</body>
</html>
```